Veltrano.co - Polar Expeditions Specialists

We need a modern, visually striking business card for Veltrano.co, a company specialized in selling expedition cruises to the most remote regions on Earth, with a focus on the Arctic and Antarctica. The design should instantly communicate that the cardholder is an expert in polar travel. Use clean, premium aesthetics with cool tones like icy blue and white, possibly incorporating polar imagery (ice, glaciers, penguins, etc.)

Attached the logo

Contact Information for Business Card

Feels high-end and trustworthy.. Visually memorable — encourages people to keep it

Colors
0054AA
0677BA
7BADD7
CADEEF
E8F1F8

Requirements
Must have
• ice, glaciers, penguins, montains
Nice to have
• modern, transparente,

```html
<!DOCTYPE html>
<html lang="en">
<head>
<meta charset="UTF-8">
<title>Veltrano.co – Business Card</title>
<link href="https://fonts.googleapis.com/css2?family=Poppins:wght@400;500;600;700&display=swap" rel="stylesheet">
<style>
  :root {
    --page-bg: #e6e9ee;
    --card-white: #ffffff;
    --brand-blue: #2f6fbe;
    --band-blue: #3d68b5;
    --back-blue: #3b7cc4;
    --back-blue-deep: #336fb6;
    --back-mark: #6d9fd8;
    --text-white: #ffffff;
    --text-soft: #dfe8f6;
  }
  * { box-sizing: border-box; margin: 0; padding: 0; }
  html, body { width: 1200px; height: 900px; overflow: hidden; }
  body {
    background: var(--page-bg);
    font-family: "Poppins", sans-serif;
    display: flex;
    align-items: center;
    justify-content: center;
    gap: 40px;
  }
  .card {
    position: relative;
    width: 540px;
    height: 309px;
    border-radius: 4px;
    overflow: hidden;
    box-shadow: 0 6px 18px rgba(20, 40, 80, 0.18);
  }
  .card-front { background: var(--card-white); }
  .card-back {
    background: linear-gradient(150deg, var(--back-blue) 0%, var(--back-blue-deep) 100%);
    display: flex;
    flex-direction: column;
    align-items: center;
    justify-content: center;
  }
  .brand { position: absolute; left: 44px; top: 40px; }
  .brand-name {
    display: flex;
    align-items: center;
    gap: 12px;
    font-size: 52px;
    font-weight: 700;
    line-height: 1;
    color: var(--brand-blue);
    letter-spacing: 0.5px;
  }
  .brand-dot {
    width: 22px; height: 22px;
    border-radius: 50%;
    background: var(--brand-blue);
  }
  .brand-tagline {
    margin-top: 8px;
    font-size: 16px;
    font-weight: 600;
    color: var(--brand-blue);
    letter-spacing: 0.3px;
  }
  .info-band {
    position: absolute;
    left: 0; right: 0;
    top: 172px;
    height: 92px;
    background: var(--band-blue);
    display: flex;
    align-items: center;
    padding: 0 32px;
    color: var(--text-white);
  }
  .holder { width: 190px; }
  .holder-name { font-size: 20px; font-weight: 700; line-height: 1.2; }
  .holder-role { font-size: 13px; font-weight: 400; color: var(--text-soft); }
  .divider {
    width: 1px; height: 62px;
    background: var(--text-white);
    margin: 0 22px;
  }
  .contacts { list-style: none; font-size: 13px; line-height: 1.6; }
  .contacts li { display: flex; align-items: center; gap: 8px; }
  .contacts svg { width: 12px; height: 12px; fill: none; stroke: var(--text-white); stroke-width: 2; }
  .back-name {
    font-size: 60px;
    font-weight: 700;
    color: var(--back-mark);
    line-height: 1;
  }
  .back-tagline {
    margin-top: 8px;
    font-size: 17px;
    font-weight: 500;
    color: var(--back-mark);
  }
</style>
</head>
<body>
  <section class="card card-front">
    <div class="brand">
      <div class="brand-name"><span class="brand-dot"></span>Veltrano.co</div>
      <div class="brand-tagline">Polar Expeditions Specialists</div>
    </div>
    <div class="info-band">
      <div class="holder">
        <div class="holder-name">Marcus Ellery</div>
        <div class="holder-role">Managing Director</div>
      </div>
      <div class="divider"></div>
      <ul class="contacts">
        <li>
          <svg viewBox="0 0 24 24"><path d="M5 3h4l2 5-3 2a12 12 0 0 0 6 6l2-3 5 2v4a2 2 0 0 1-2 2A18 18 0 0 1 3 5a2 2 0 0 1 2-2z"/></svg>
          (555)214-7380
        </li>
        <li>
          <svg viewBox="0 0 24 24"><rect x="3" y="5" width="18" height="14" rx="1"/><path d="M3 6l9 7 9-7"/></svg>
          info@veltrano.co
        </li>
        <li>
          <svg viewBox="0 0 24 24"><circle cx="12" cy="12" r="9"/><path d="M3 12h18M12 3c3 3 3 15 0 18M12 3c-3 3-3 15 0 18"/></svg>
          www.veltrano.co
        </li>
      </ul>
    </div>
  </section>

  <section class="card card-back">
    <div class="back-name">Veltrano.co</div>
    <div class="back-tagline">Polar Expeditions Specialists</div>
  </section>
</body>
</html>
```